English and Spanish Language School Needs a Business Card

Need a business card design a startup company called Maribel Language School. The company will offer English and Spanish conversational level courses designed to make the learner feel comfortable with grammar and vocabulary. We would like to see a logo with some colour that should communicate learning, growth.

Target Market(s)

Consumers and businesses

Industry/Entity Type

Education

Contact Information for Business Card

TBD

Font styles to use
Serif

Requirements
Must have
• Include the following
• Logo
• Name
• Title
• Cellphone Number
• Office Phone number
• Email address
• Office Address

```html
<!DOCTYPE html>
<html lang="en">
<head>
<meta charset="UTF-8">
<title>Maribel Language School – Business Card</title>
<link rel="stylesheet" href="https://fonts.googleapis.com/css2?family=Open+Sans:wght@400;600;700&display=swap">
<style>
  :root {
    --brand-red: #c8202b;
    --brand-teal: #00a0ad;
    --ink: #3a3a3a;
    --card: #ffffff;
    --backdrop: #ebe8e5;
  }
  * { margin: 0; padding: 0; box-sizing: border-box; }
  html, body {
    width: 1200px;
    height: 900px;
    overflow: hidden;
    background: var(--backdrop);
    font-family: "Open Sans", Arial, sans-serif;
  }
  .canvas { position: relative; width: 1200px; height: 900px; }

  .card {
    position: absolute;
    background: var(--card);
    box-shadow: 0 6px 18px rgba(0,0,0,0.12);
    overflow: hidden;
  }

  /* Front card */
  .card-front { left: 238px; top: 62px; width: 555px; height: 342px; }
  .band-top { position: absolute; left: 0; top: 0; width: 100%; height: 26px; background: var(--brand-teal); }
  .band-bottom { position: absolute; left: 0; bottom: 0; width: 100%; height: 23px; background: var(--brand-red); }

  .brand-vertical {
    position: absolute;
    left: 72px; top: 174px;
    width: 0; height: 0;
  }
  .brand-vertical .brand-name {
    position: absolute;
    left: 0; top: 0;
    transform: translate(-50%, -50%) rotate(-90deg);
    white-space: nowrap;
    text-align: center;
    color: var(--brand-red);
    font-weight: 600;
    font-size: 19px;
    line-height: 1.15;
  }

  .divider {
    position: absolute;
    left: 167px; top: 90px;
    width: 1px; height: 168px;
    background: var(--brand-teal);
  }

  .details { position: absolute; left: 207px; top: 88px; color: var(--ink); }
  .person-name { font-size: 18px; font-weight: 700; line-height: 1.2; }
  .person-name .first { color: var(--brand-red); }
  .person-name .last { color: var(--brand-teal); }
  .person-title { font-size: 15px; margin-top: 1px; }
  .address { font-size: 15px; line-height: 20px; margin-top: 14px; }
  .contacts { list-style: none; margin-top: 15px; font-size: 15px; line-height: 20px; }
  .contacts li { display: flex; align-items: center; }
  .contacts svg { width: 11px; height: 11px; margin-right: 9px; fill: var(--brand-red); flex: none; }

  /* Back card */
  .card-back { left: 457px; top: 519px; width: 560px; height: 342px; display: flex; align-items: center; justify-content: center; }
  .brand-centered {
    color: var(--brand-red);
    font-weight: 600;
    font-size: 34px;
    letter-spacing: -0.3px;
  }
</style>
</head>
<body>
<main class="canvas">

  <section class="card card-front" aria-label="Business card, front">
    <div class="band-top"></div>

    <div class="brand-vertical">
      <div class="brand-name">Maribel<br>Language School</div>
    </div>

    <div class="divider"></div>

    <div class="details">
      <p class="person-name"><span class="first">Daniel</span> <span class="last">Carter</span></p>
      <p class="person-title">Managing Director</p>
      <p class="address">12345, Address Goes Here<br>Country Name, 123456.</p>
      <ul class="contacts">
        <li>
          <svg viewBox="0 0 24 24" aria-hidden="true"><path d="M6.6 10.8a15.1 15.1 0 0 0 6.6 6.6l2.2-2.2c.3-.3.7-.4 1-.2 1.1.4 2.3.6 3.6.6.6 0 1 .4 1 1V20c0 .6-.4 1-1 1A17 17 0 0 1 3 4c0-.6.4-1 1-1h3.5c.6 0 1 .4 1 1 0 1.3.2 2.5.6 3.6.1.3 0 .7-.2 1z"/></svg>
          044-987 654 321
        </li>
        <li>
          <svg viewBox="0 0 24 24" aria-hidden="true"><path d="M7 1h10a2 2 0 0 1 2 2v18a2 2 0 0 1-2 2H7a2 2 0 0 1-2-2V3a2 2 0 0 1 2-2zm0 3v14h10V4zm5 15.5a1 1 0 1 0 0 2 1 1 0 0 0 0-2z"/></svg>
          hello@maribelschool.com
        </li>
        <li>
          <svg viewBox="0 0 24 24" aria-hidden="true"><path d="M2 5h20v14H2zm2 2v.5l8 5 8-5V7zm0 2.8V17h16V9.8l-8 5z"/></svg>
          www.maribelschool.com
        </li>
      </ul>
    </div>

    <div class="band-bottom"></div>
  </section>

  <section class="card card-back" aria-label="Business card, back">
    <p class="brand-centered">Maribel Language School</p>
  </section>

</main>
</body>
</html>
```